Personal Business Card

I am an award winning banjo player who plays with two different professional bands. My experiences include studio recordings for other artists and played the theme song for the Creature Channel's "Frontier Tundra Men". I am ready to take my career to the next level and would like something that will look professional. it is important to me to have a banjo on the card. If possible my accomplishments to be put on back of card.

Industry/Entity Type

Artists

Contact Information for Business Card

Corbin Hale
cell 555-316-2084
email corbinhalebanjo@pickmail.test

2008 AZ Banjo Champion
2008 Pinefolk Banjo Champion
2010 AZ Banjo Champion
2010 Sawyer Creek Roundup Morland Banjo Champion
2010 Cedar Hollow Gathering Banjo Finalist

```html
<!DOCTYPE html>
<html lang="en">
<head>
<meta charset="utf-8">
<title>Corbin Hale – Business Card</title>
<link href="https://fonts.googleapis.com/css2?family=Ubuntu:wght@400;700&display=swap" rel="stylesheet">
<style>
  :root {
    --page-bg: #d4d4d4;
    --card-dark: #3b3c3e;
    --card-mid: #47484a;
    --ink-light: #f2f2f2;
    --photo-light: #b9b9b9;
    --photo-dark: #5a5656;
    --icon-fill: #8c8d8f;
  }
  * { margin: 0; padding: 0; box-sizing: border-box; }
  html, body { width: 1200px; height: 1000px; overflow: hidden; }
  body {
    background: var(--page-bg);
    font-family: "Ubuntu", sans-serif;
    color: var(--ink-light);
    position: relative;
  }
  .card {
    position: absolute;
    left: 215px;
    width: 770px;
    height: 440px;
    border-radius: 4px;
    background: linear-gradient(160deg, var(--card-mid), var(--card-dark) 60%);
    box-shadow: 0 4px 14px rgba(0,0,0,0.25);
    overflow: hidden;
  }
  .card--back { top: 40px; }
  .card--front { top: 520px; }

  .achievements { position: absolute; list-style: none; font-size: 19px; }
  .achievements li { line-height: 1.5; }
  .achievements--early { left: 40px; top: 30px; }
  .achievements--late { left: 250px; top: 290px; }

  .banjo-icon { position: absolute; left: 570px; top: 70px; width: 140px; height: 190px; }

  .banjo-photo { position: absolute; left: 30px; top: 36px; width: 620px; height: 210px; }

  .contact { position: absolute; right: 50px; top: 262px; text-align: right; }
  .contact__name { font-size: 36px; font-weight: 700; margin-bottom: 14px; }
  .contact__line { font-size: 22px; line-height: 1.7; }
</style>
</head>
<body>

<section class="card card--back" aria-label="Card back – achievements">
  <ul class="achievements achievements--early">
    <li>2008 AZ Banjo Champion</li>
    <li>2008 Pinefolk Banjo Champion</li>
  </ul>
  <svg class="banjo-icon" viewBox="0 0 140 190" role="img" aria-label="White banjo silhouette illustration">
    <rect width="140" height="190" rx="8" fill="var(--icon-fill)"/>
  </svg>
  <ul class="achievements achievements--late">
    <li>2010 AZ Banjo Champion</li>
    <li>2010 Sawyer Creek Roundup Morland Banjo Champion</li>
    <li>2010 Cedar Hollow Gathering Banjo Finalist</li>
  </ul>
</section>

<section class="card card--front" aria-label="Card front – contact">
  <svg class="banjo-photo" viewBox="0 0 620 210" role="img" aria-label="Photograph of a five-string banjo lying diagonally across the card">
    <defs>
      <radialGradient id="banjoTone" cx="30%" cy="55%" r="70%">
        <stop offset="0" stop-color="var(--photo-light)"/>
        <stop offset="1" stop-color="var(--photo-dark)"/>
      </radialGradient>
    </defs>
    <rect width="620" height="210" rx="10" fill="url(#banjoTone)" opacity="0.85"/>
  </svg>
  <div class="contact">
    <p class="contact__name">Corbin Hale</p>
    <p class="contact__line">cell :&nbsp; 555-316-2084</p>
    <p class="contact__line">email : corbinhalebanjo@pickmail.test</p>
  </div>
</section>

</body>
</html>
```